Simple and clean

We need a business card design for a new company called Dwelling Hawk. It is a search engine to find current properties for sale or rent in New Zealand market.
We have already a colour scheme that we would like people to use.
Light brown: #D4CCB0
Light green: #D6E4D4
Green: #669966
Black/White
It is OK to divert from this colour scheme slightly as long as there is a green component to the business card.
Final design should be clean, simple and should communicate the nature of the business.
Target Market(s)
- First home buyers
- Real estate agents
- People seeking rentals
Industry/Entity Type
Business
Requirements
Must have
- Use those or similar colours.
Light brown: #D4CCB0
Light green: #D6E4D4
Green: #669966
Black/White

```html
<!DOCTYPE html>
<html lang="en">
<head>
<meta charset="UTF-8">
<title>Dwelling Hawk – Business Card</title>
<link href="https://fonts.googleapis.com/css2?family=Arimo:wght@700&display=swap" rel="stylesheet">
<style>
  :root {
    --page-bg: #ffffff;
    --card-green: #bfe4bb;
    --card-green-light: #c9eac5;
    --ink-green: #4a7f4c;
    --ink-dark: #1f2a1f;
  }
  html, body {
    margin: 0;
    width: 1200px;
    height: 899px;
    overflow: hidden;
    background: var(--page-bg);
    font-family: "Arimo", Arial, sans-serif;
  }
  .business-card {
    position: absolute;
    left: 150px;
    top: 210px;
    width: 900px;
    height: 480px;
    background: linear-gradient(135deg, var(--card-green) 0%, var(--card-green-light) 55%, var(--card-green) 100%);
    box-shadow: 0 10px 30px rgba(0, 0, 0, 0.15);
  }
  .brand-name {
    position: absolute;
    left: 42px;
    top: 240px;
    transform: translate(-50%, -50%) rotate(-90deg);
    white-space: nowrap;
    font-size: 40px;
    font-weight: 700;
    color: var(--ink-dark);
    letter-spacing: -0.5px;
  }
  .contact-block {
    position: absolute;
    left: 427px;
    transform: translateX(-50%);
    white-space: nowrap;
    font-weight: 700;
    color: var(--ink-green);
    text-align: center;
    margin: 0;
    letter-spacing: -0.5px;
  }
  .person-name { top: 100px; font-size: 54px; }
  .person-role { top: 165px; font-size: 30px; left: 445px; }
  .phone { top: 222px; font-size: 34px; }
  .email { top: 268px; font-size: 33px; }
  .website { top: 380px; font-size: 36px; }
</style>
</head>
<body>
  <div class="business-card">
    <div class="brand-name">Dwelling Hawk</div>
    <p class="contact-block person-name">Rowan Tate</p>
    <p class="contact-block person-role">Director</p>
    <p class="contact-block phone">000 000 000</p>
    <p class="contact-block email">rowan@dwellinghawk.co.nz</p>
    <p class="contact-block website">www.dwellinghawk.co.nz</p>
  </div>
</body>
</html>
```